Tide & Thistle Website Creation For Online Spirits Sales via MerrowVats.com

Want a Website developed that I will use to partner with Merrow Vats to sell my signature rum online. Merrow Vats will add the final code to make the website an e-commerce site. Website should have links to Social media pages, recipies, About, news and events, products. I have he domain name already just need a designer to make the website look professional. Need website capable of being viewed on iPhone and Android devices. Please use the color scheme that is on the label. The brand motto is: Celebrate Life With Family old and new friends. The bottle sent in the images will be replaced with and actual high resolution image of the bottle when it is produce on 27 DEC 21. Can give the selected designer access to develop the website. I have the hostbramble.com domain name. Final code will be added by a designer from MerrowVats.com to make it a e-commerce store.
Updates

I added more information to refine the design I wanted. I should have had this information available to the designers when I started the project.

Target Market(s)

Target Market is 25-50 year old who drink rum

Industry/Entity Type

Spirits. Using Website to sell Rum online

Number of Pages Required

1 page

Font styles to use
Sans Serif

Colors
00AB8E
00BBA5
67D7C9
C6EFE9
E9F9F6

Requirements
Must have
• Must look elegant and of high class. Rum is being market as a premium unnamed rum.
Nice to have
• Video of people drinking, smiling and celebrating

```html
<!DOCTYPE html>
<html lang="en">
<head>
<meta charset="utf-8">
<title>Tide &amp; Thistle — Premium Rum</title>
<link href="https://fonts.googleapis.com/css2?family=Playfair+Display:wght@400;700;900&family=Montserrat:wght@400;500;600;700&display=swap" rel="stylesheet">
<style>
:root{
  --teal:#00ab8e;
  --teal-2:#00bba5;
  --teal-3:#67d7c9;
  --mint:#c6efe9;
  --mint-light:#e9f9f6;
  --ink:#1a1a1a;
  --grey:#555;
  --night:#0b0b0b;
  --white:#fff;
  --serif:'Playfair Display',Georgia,serif;
  --sans:'Montserrat',Arial,sans-serif;
}
*{margin:0;padding:0;box-sizing:border-box}
html,body{width:1200px;height:3688px;overflow:hidden;background:var(--white)}
body{position:relative;font-family:var(--sans);color:var(--ink)}
.abs{position:absolute}

/* header */
.phone{left:112px;top:56px;color:var(--teal);font-weight:700;font-size:19px;display:flex;align-items:center;gap:8px}
.brand{left:450px;top:12px;width:300px;text-align:center}
.brand-mark{width:66px;height:66px;border-radius:50%;background:var(--ink);margin:0 auto 10px}
.brand-name{font-family:var(--serif);font-weight:700;font-size:30px;color:var(--ink);letter-spacing:.5px;white-space:nowrap}
.search{left:795px;top:47px;width:293px;height:42px;background:var(--mint-light);border-radius:3px;display:flex;align-items:center;justify-content:space-between;padding:0 16px;font-size:12px;color:#555}
.nav{left:112px;top:135px;width:976px;height:57px;background:var(--night);display:flex;align-items:center;padding:0 24px;z-index:3}
.nav a{font-family:var(--serif);color:var(--white);text-decoration:none;font-size:14px;letter-spacing:1px;margin-right:38px}
.nav .icons{margin-left:auto;display:flex;gap:18px;align-items:center}

/* hero */
.hero{left:0;top:165px;width:1200px;height:660px}
.hero-photo{left:650px;top:294px;width:524px;height:491px;background:radial-gradient(ellipse at 45% 50%,#c9822a 0%,#6a3d12 38%,#1a1410 70%,var(--night) 100%);border-radius:4px}
.hero-title{left:112px;top:362px;font-family:var(--serif);font-weight:900;font-size:38px;line-height:49px;color:var(--teal);z-index:2}
.hero-text{left:112px;top:475px;width:525px;color:var(--white);font-size:14px;line-height:24px;font-weight:500;z-index:2}
.btn{background:var(--teal);color:var(--white);font-weight:600;display:flex;align-items:center;justify-content:center;border-radius:2px}
.hero-btn{left:112px;top:561px;width:151px;height:42px;font-size:15px}
.dots{left:112px;top:638px;display:flex;gap:5px;align-items:center}
.dots i{width:9px;height:9px;border-radius:50%;background:var(--white);display:block}
.dots i.on{width:14px;height:14px}

/* headings */
.section-title{width:1200px;left:0;text-align:center;font-family:var(--serif);font-size:42px;font-weight:700;color:var(--ink)}
.section-title span{color:var(--teal);font-weight:400}

/* products */
.card{top:1088px;width:223px;height:361px;border:1px solid #e6e6e6;background:var(--white)}
.bottle{top:945px;width:130px;height:330px;background:linear-gradient(180deg,#e9e2cf 0%,#d9d2bd 22%,#c77a2a 40%,#a45a18 75%,#7c4210 100%);border-radius:30px 30px 20px 20px}
.price{top:1303px;width:223px;text-align:center;color:var(--teal);font-size:15px;font-weight:500}
.pname{top:1333px;width:223px;text-align:center;font-family:var(--serif);font-size:15px;line-height:22px;color:#222}
.stars{top:1386px;width:223px;text-align:center;color:var(--teal);font-size:16px;letter-spacing:2px}
.cart-btn{top:1429px;width:177px;height:39px;font-size:14px}
.arrow{top:1191px;width:38px;height:38px}

/* video band */
.video{left:0;top:1585px;width:1200px;height:725px;background:radial-gradient(ellipse at 50% 45%,#5a4632 0%,#30261c 45%,#15110d 100%)}
.video-text{left:0;top:1838px;width:1200px;text-align:center;font-family:var(--serif);font-size:45px;line-height:60px;color:var(--white);font-weight:500}
.video-text .accent{color:var(--teal)}
.video-btn{left:494px;top:2062px;width:212px;height:57px;font-size:18px;gap:10px;font-weight:700}

/* news */
.news{top:2434px;width:305px;height:413px;background:var(--white);box-shadow:0 2px 8px rgba(0,0,0,.12)}
.news-img{width:305px;height:197px}
.news-date{left:24px;top:222px;font-size:14px;font-weight:600;display:flex;gap:8px;align-items:center}
.news-title{left:24px;top:260px;width:260px;font-family:var(--serif);font-weight:700;font-size:17px;line-height:24px;color:#333}
.news-text{left:24px;top:318px;width:265px;font-size:15px;line-height:23px;color:var(--grey)}

/* newsletter */
.footer-bg{left:0;top:2900px;width:1200px;height:788px;background:var(--mint-light)}
.news-brand{left:112px;top:3029px;width:222px;text-align:center}
.nl-title{left:461px;top:3016px;font-family:var(--serif);font-size:31px;color:var(--teal);font-weight:700}
.nl-sub{left:461px;top:3064px;font-size:15px;font-weight:600}
.nl-input{left:461px;top:3096px;width:490px;height:46px;background:var(--white);border:1px solid #ddd;box-shadow:0 2px 4px rgba(0,0,0,.15);font-size:14px;color:#555;padding-left:28px;display:flex;align-items:center}
.nl-btn{left:962px;top:3096px;width:126px;height:46px;font-size:15px;font-weight:700;box-shadow:0 2px 4px rgba(0,0,0,.2)}
.rule{left:0;width:1200px;height:1px;background:var(--teal)}

/* footer columns */
.col{top:3238px;border-left:3px solid var(--teal);padding-left:16px}
.col h4{font-family:var(--serif);font-weight:400;font-size:20px;color:#222;margin-bottom:20px;letter-spacing:.5px}
.col li{list-style:none;font-size:15px;color:#444;line-height:31px}
.contact-row{left:810px;display:flex;gap:14px;font-size:15px;color:#444;line-height:23px}
.social{top:3465px;width:38px;height:38px;border:2px solid var(--teal);border-radius:50%}
.pay{top:3623px;width:47px;height:29px;border-radius:3px}
.copy{right:114px;top:3625px;font-size:15px;color:#444}
</style>
</head>
<body>

<!-- header -->
<div class="abs phone">
  <svg width="16" height="16" viewBox="0 0 24 24"><path fill="#00ab8e" d="M6.6 10.8a15.1 15.1 0 0 0 6.6 6.6l2.2-2.2c.3-.3.7-.4 1-.2 1.1.4 2.3.6 3.6.6.6 0 1 .4 1 1V20c0 .6-.4 1-1 1C10.6 21 3 13.4 3 4c0-.6.4-1 1-1h3.5c.6 0 1 .4 1 1 0 1.3.2 2.5.6 3.6.1.3 0 .7-.2 1z"/></svg>
  555 218 4470
</div>
<div class="abs brand">
  <div class="brand-mark"></div>
  <div class="brand-name">Tide &amp; Thistle</div>
</div>
<div class="abs search">
  <span>Search products...</span>
  <svg width="13" height="13" viewBox="0 0 24 24"><circle cx="10" cy="10" r="7" stroke="#111" stroke-width="3" fill="none"/><path d="M15 15l6 6" stroke="#111" stroke-width="3"/></svg>
</div>
<nav class="abs nav">
  <a>HOME</a><a>RECIPES</a><a>ABOUT</a><a>NEWS</a><a>EVENTS</a><a>PRODUCTS</a><a>CONTACT US</a>
  <div class="icons">
    <svg width="24" height="26" viewBox="0 0 24 26"><rect x="3" y="11" width="18" height="13" rx="2" stroke="#fff" stroke-width="2" fill="none"/><path d="M7 11V7a5 5 0 0 1 10 0" stroke="#fff" stroke-width="2" fill="none"/></svg>
    <svg width="32" height="28" viewBox="0 0 32 28"><path d="M1 3h5l4 15h16l3-11H8" stroke="#fff" stroke-width="2" fill="none"/><circle cx="12" cy="24" r="2" fill="#fff"/><circle cx="24" cy="24" r="2" fill="#fff"/><circle cx="27" cy="5" r="5" fill="#00ab8e"/></svg>
  </div>
</nav>

<!-- hero -->
<svg class="abs hero" viewBox="0 0 1200 660" preserveAspectRatio="none" aria-hidden="true">
  <path fill="#0b0b0b" d="M0 0H1200V648L1150 644 1090 652 1010 640 940 650 880 638 820 646 760 634 700 640 640 628 580 636 520 624 460 632 400 620 340 626 280 616 220 622 160 610 100 618 40 608 0 614Z"/>
</svg>
<div class="abs hero-photo" role="img" aria-label="Rum bottle and a glass of rum on a silver tray held by a waiter"></div>
<h1 class="abs hero-title">Celebrate Life With Family,<br>old and new friends</h1>
<p class="abs hero-text">Lorem Ipsum is simply dummy text of the printing and typeset-ting industry. Lorem Ipsum has been the industry's standard dummy text ever since the 1500s,</p>
<div class="abs btn hero-btn">Shop Now</div>
<div class="abs dots"><i></i><i></i><i class="on"></i><i></i><i></i></div>

<!-- products -->
<h2 class="abs section-title" style="top:832px">Our <span>Products</span></h2>
<svg class="abs arrow" style="left:36px" viewBox="0 0 38 38"><circle cx="19" cy="19" r="17" stroke="#333" stroke-width="1.5" fill="none"/><path d="M22 12l-7 7 7 7" stroke="#333" stroke-width="1.5" fill="none"/></svg>
<svg class="abs arrow" style="left:1126px" viewBox="0 0 38 38"><circle cx="19" cy="19" r="17" stroke="#333" stroke-width="1.5" fill="none"/><path d="M16 12l7 7-7 7" stroke="#333" stroke-width="1.5" fill="none"/></svg>

<div class="abs card" style="left:109px"></div>
<div class="abs card" style="left:361px"></div>
<div class="abs card" style="left:613px"></div>
<div class="abs card" style="left:865px"></div>

<div class="abs bottle" style="left:155px" role="img" aria-label="Rum bottle"></div>
<div class="abs bottle" style="left:407px" role="img" aria-label="Rum bottle"></div>
<div class="abs bottle" style="left:659px" role="img" aria-label="Rum bottle"></div>
<div class="abs bottle" style="left:911px" role="img" aria-label="Rum bottle"></div>

<div class="abs price" style="left:109px">$15.59</div>
<div class="abs price" style="left:361px">$15.59</div>
<div class="abs price" style="left:613px">$15.59</div>
<div class="abs price" style="left:865px">$15.59</div>
<div class="abs pname" style="left:109px">Nemo enim ipsam<br>voluptatem quia voluptas</div>
<div class="abs pname" style="left:361px">Nemo enim ipsam<br>voluptatem quia voluptas</div>
<div class="abs pname" style="left:613px">Nemo enim ipsam<br>voluptatem quia voluptas</div>
<div class="abs pname" style="left:865px">Nemo enim ipsam<br>voluptatem quia voluptas</div>
<div class="abs stars" style="left:109px">★★★★★</div>
<div class="abs stars" style="left:361px">★★★★★</div>
<div class="abs stars" style="left:613px">★★★★★</div>
<div class="abs stars" style="left:865px">★★★★★</div>
<div class="abs btn cart-btn" style="left:132px">ADD TO CART</div>
<div class="abs btn cart-btn" style="left:384px">ADD TO CART</div>
<div class="abs btn cart-btn" style="left:636px">ADD TO CART</div>
<div class="abs btn cart-btn" style="left:888px">ADD TO CART</div>

<!-- video band -->
<div class="abs video" role="img" aria-label="Dim tavern scene of a man drinking from a bottle, video still"></div>
<svg class="abs" style="left:0;top:1580px" width="1200" height="40" viewBox="0 0 1200 40" preserveAspectRatio="none" aria-hidden="true"><path fill="#fff" d="M0 0H1200V6L1140 12 1080 4 1010 14 950 6 880 16 810 8 740 18 670 10 600 20 530 12 460 22 390 12 320 24 250 14 180 26 110 16 40 28 0 22Z"/></svg>
<svg class="abs" style="left:0;top:2280px" width="1200" height="40" viewBox="0 0 1200 40" preserveAspectRatio="none" aria-hidden="true"><path fill="#fff" d="M0 24L60 18 130 26 200 16 270 24 340 14 410 22 480 12 550 20 620 10 690 18 760 8 830 16 900 6 970 14 1040 4 1110 12 1200 2V40H0Z"/></svg>
<div class="abs video-text">Neque porro quisquam est<br><span class="accent">dolorem ipsum quia dolor sit amet,</span><br>consectetur, adipisci velit...</div>
<div class="abs btn video-btn">WATCH VIDEO
  <svg width="26" height="26" viewBox="0 0 26 26"><circle cx="13" cy="13" r="11" stroke="#fff" stroke-width="2" fill="none"/><path d="M10 8l8 5-8 5z" fill="#fff"/></svg>
</div>

<!-- news -->
<h2 class="abs section-title" style="top:2352px">Latest <span>News</span></h2>
<div class="abs news" style="left:112px">
  <div class="news-img" role="img" aria-label="Two hands toasting glasses of rum" style="background:linear-gradient(135deg,#3a2410,#b8742e 50%,#4a2c12)"></div>
  <div class="abs news-date"><svg width="13" height="13" viewBox="0 0 14 14"><rect x="1" y="2" width="12" height="11" rx="1" fill="#444"/><rect x="2.5" y="5" width="9" height="6.5" fill="#fff"/></svg>DEC 17, 2021</div>
  <div class="abs news-title">Nemo enim ipsam voluptate quia voluptas sit</div>
  <div class="abs news-text">Sed ut perspiciatis unde omnis iste natus sit voluptatem accusantium doloremque laudantium</div>
</div>
<div class="abs news" style="left:447px">
  <div class="news-img" role="img" aria-label="Glasses of rum clinking together" style="background:linear-gradient(135deg,#1b2a44,#6d5a44 50%,#2a3550)"></div>
  <div class="abs news-date"><svg width="13" height="13" viewBox="0 0 14 14"><rect x="1" y="2" width="12" height="11" rx="1" fill="#444"/><rect x="2.5" y="5" width="9" height="6.5" fill="#fff"/></svg>DEC 17, 2021</div>
  <div class="abs news-title">Nemo enim ipsam voluptate quia voluptas sit</div>
  <div class="abs news-text">Sed ut perspiciatis unde omnis iste natus sit voluptatem accusantium doloremque laudantium</div>
</div>
<div class="abs news" style="left:782px">
  <div class="news-img" role="img" aria-label="Friends celebrating with drinks at a bar" style="background:linear-gradient(135deg,#2a1a2a,#8a5a4a 50%,#2c3a1e)"></div>
  <div class="abs news-date"><svg width="13" height="13" viewBox="0 0 14 14"><rect x="1" y="2" width="12" height="11" rx="1" fill="#444"/><rect x="2.5" y="5" width="9" height="6.5" fill="#fff"/></svg>DEC 17, 2021</div>
  <div class="abs news-title">Nemo enim ipsam voluptate quia voluptas sit</div>
  <div class="abs news-text">Sed ut perspiciatis unde omnis iste natus sit voluptatem accusantium doloremque laudantium</div>
</div>

<!-- newsletter & footer -->
<div class="abs footer-bg"></div>
<svg class="abs" style="left:0;top:2895px" width="1200" height="50" viewBox="0 0 1200 50" preserveAspectRatio="none" aria-hidden="true"><path fill="#fff" d="M0 0H1200V30L1130 20 1060 32 990 22 920 34 850 24 780 36 710 26 640 38 570 28 500 40 430 30 360 42 290 32 220 44 150 34 80 46 0 38Z"/></svg>
<div class="abs news-brand">
  <div class="brand-mark"></div>
  <div class="brand-name">Tide &amp; Thistle</div>
</div>
<div class="abs nl-title">Join our Newsletter</div>
<div class="abs nl-sub">Subscribe to our mailing list to receive updates</div>
<div class="abs nl-input">Enter your E - mail</div>
<div class="abs btn nl-btn">SUBSCRIBE</div>
<div class="abs rule" style="top:3186px"></div>

<div class="abs col" style="left:92px">
  <h4>MY ACCOUNT</h4>
  <ul><li>My Orders</li><li>My Bills</li><li>My Addresses</li><li>My Personal Information</li><li>My Vouchers</li><li>Site Map</li><li>Blog</li></ul>
</div>
<div class="abs col" style="left:315px">
  <h4>INFORMATION</h4>
  <ul><li>New products</li><li>Contact Us</li><li>Regulations</li><li>FAQ</li><li>Our stores</li></ul>
</div>
<div class="abs col" style="left:568px">
  <h4>QUICK LINKS</h4>
  <ul><li>Home</li><li>Recipes</li><li>About</li><li>News</li><li>Events</li><li>Products</li><li>Contact Us</li></ul>
</div>
<div class="abs col" style="left:785px;height:300px">
  <h4>CONTACT US</h4>
</div>
<div class="abs contact-row" style="top:3296px">
  <svg width="20" height="24" viewBox="0 0 20 24"><path fill="#00ab8e" d="M10 0a8 8 0 0 0-8 8c0 6 8 16 8 16s8-10 8-16a8 8 0 0 0-8-8zm0 11a3 3 0 1 1 0-6 3 3 0 0 1 0 6z"/></svg>
  <span>Harbour Quay Lanes<br>42-118 enim ipsam vo-<br>luptatem quia voluptas sit</span>
</div>
<div class="abs contact-row" style="top:3377px">
  <svg width="22" height="22" viewBox="0 0 24 24"><path fill="#00ab8e" d="M6.6 10.8a15.1 15.1 0 0 0 6.6 6.6l2.2-2.2c.3-.3.7-.4 1-.2 1.1.4 2.3.6 3.6.6.6 0 1 .4 1 1V20c0 .6-.4 1-1 1C10.6 21 3 13.4 3 4c0-.6.4-1 1-1h3.5c.6 0 1 .4 1 1 0 1.3.2 2.5.6 3.6.1.3 0 .7-.2 1z"/></svg>
  <span>Phone: +1 (555) 301-7762</span>
</div>
<div class="abs contact-row" style="top:3421px">
  <svg width="20" height="20" viewBox="0 0 20 20"><rect x="0" y="3" width="20" height="14" rx="1" fill="#00ab8e"/><path d="M1 4l9 7 9-7" stroke="#e9f9f6" stroke-width="1.5" fill="none"/></svg>
  <span>Email: hello@tidethistle.com</span>
</div>
<div class="abs social" style="left:811px" aria-label="Social link"></div>
<div class="abs social" style="left:864px" aria-label="Social link"></div>
<div class="abs social" style="left:916px" aria-label="Social link"></div>

<div class="abs rule" style="top:3561px"></div>
<div class="abs pay" style="left:112px;background:#d9d9d9" aria-label="Payment method"></div>
<div class="abs pay" style="left:167px;background:#2b3f7c" aria-label="Payment method"></div>
<div class="abs pay" style="left:222px;background:#d9d9d9" aria-label="Payment method"></div>
<div class="abs pay" style="left:277px;background:#3a7bc8" aria-label="Payment method"></div>
<div class="abs copy">Tide &amp; Thistle © 2021. All Rights Reserved.</div>

</body>
</html>
```